New Business Card Design Project

We would like a business card that represents the sale of boat, home, auto, and life insurance.

The logo can change colors to meet the look of the design if needed.

Industry/Entity Type

Business

```html
<!DOCTYPE html>
<html lang="en">
<head>
<meta charset="utf-8">
<title>Harborline Financial business card</title>
<link rel="stylesheet" href="https://fonts.googleapis.com/css2?family=Montserrat:wght@600&family=Open+Sans:wght@400;600&display=swap">
<style>
  :root {
    --stage: #dedbd7;
    --card: #0c0d0f;
    --ink: #f2f2f2;
    --muted: #c9cbcd;
    --accent: #3a8fb7;
    --strip: #e4e4e4;
    --rule: #6a6d70;
  }
  * { box-sizing: border-box; margin: 0; padding: 0; }
  html, body { width: 1200px; height: 768px; overflow: hidden; }
  body {
    background: var(--stage);
    font-family: "Open Sans", sans-serif;
    position: relative;
  }
  .card {
    position: absolute;
    top: 236px;
    width: 520px;
    height: 297px;
    background: var(--card);
    border-radius: 4px;
    overflow: hidden;
    box-shadow: 0 6px 18px rgba(0,0,0,0.18);
  }
  .card--front { left: 50px; }
  .card--back { left: 630px; }

  .brand {
    position: absolute;
    display: flex;
    align-items: center;
    justify-content: center;
    gap: 10px;
  }
  .brand__dot {
    flex: none;
    border-radius: 50%;
    background: var(--accent);
  }
  .brand__name {
    font-family: "Open Sans", sans-serif;
    font-weight: 600;
    color: var(--ink);
    line-height: 1;
    white-space: nowrap;
  }

  .card--front .brand { left: 0; right: 0; top: 134px; }
  .card--front .brand__dot { width: 24px; height: 24px; }
  .card--front .brand__name { font-size: 30px; }

  .card--back .brand { left: 14px; width: 258px; top: 124px; gap: 8px; }
  .card--back .brand__dot { width: 16px; height: 16px; }
  .card--back .brand__name { font-size: 20px; }

  .divider {
    position: absolute;
    left: 286px;
    top: 46px;
    width: 1px;
    height: 200px;
    background: var(--rule);
  }
  .contact {
    position: absolute;
    left: 306px;
    top: 52px;
    right: 14px;
    color: var(--muted);
  }
  .contact__name {
    font-family: "Montserrat", sans-serif;
    font-weight: 600;
    font-size: 18px;
    color: var(--ink);
  }
  .contact__title {
    font-size: 13px;
    margin-bottom: 14px;
  }
  .contact__list { list-style: none; }
  .contact__item {
    display: flex;
    align-items: center;
    gap: 8px;
    font-size: 11.5px;
    line-height: 17px;
  }
  .contact__icon { width: 11px; height: 11px; flex: none; }
  .contact__address {
    font-size: 11.5px;
    line-height: 16px;
    margin-top: 8px;
  }
  .edge-bands {
    position: absolute;
    left: 0;
    bottom: 0;
    width: 520px;
    height: 16px;
  }
</style>
</head>
<body>

  <section class="card card--front" aria-label="Card front">
    <div class="brand">
      <span class="brand__dot"></span>
      <span class="brand__name">Harborline Financial</span>
    </div>
  </section>

  <section class="card card--back" aria-label="Card back">
    <div class="brand">
      <span class="brand__dot"></span>
      <span class="brand__name">Harborline Financial</span>
    </div>

    <div class="divider"></div>

    <div class="contact">
      <div class="contact__name">Your Long Name</div>
      <div class="contact__title">Your Title</div>
      <ul class="contact__list">
        <li class="contact__item">
          <svg class="contact__icon" viewBox="0 0 12 12" fill="var(--muted)"><path d="M2 1h2.5l1 2.5-1.4 1a6 6 0 0 0 3.4 3.4l1-1.4L11 7.5V10a1 1 0 0 1-1 1A9 9 0 0 1 1 2a1 1 0 0 1 1-1z"/></svg>
          000 0 0 000 00
        </li>
        <li class="contact__item">
          <svg class="contact__icon" viewBox="0 0 12 12" fill="var(--muted)"><rect x="3" y="0.5" width="6" height="11" rx="1"/><rect x="4" y="2" width="4" height="6" fill="var(--card)"/></svg>
          (00) 0 0 0000 0000
        </li>
        <li class="contact__item">
          <svg class="contact__icon" viewBox="0 0 12 12"><rect x="0.5" y="2" width="11" height="8" fill="var(--muted)"/><path d="M0.5 2.5 6 6.5l5.5-4" fill="none" stroke="var(--card)" stroke-width="1"/></svg>
          yourname@yourwebsite.com
        </li>
        <li class="contact__item">
          <svg class="contact__icon" viewBox="0 0 12 12" fill="none" stroke="var(--muted)" stroke-width="1"><circle cx="6" cy="6" r="5"/><ellipse cx="6" cy="6" rx="2.2" ry="5"/><path d="M1 6h10"/></svg>
          www.yourwebsite.com
        </li>
      </ul>
      <p class="contact__address">Your office or residentianal address<br>in just two line with pin code.</p>
    </div>

    <svg class="edge-bands" viewBox="0 0 520 16" aria-hidden="true">
      <polygon points="0,2 248,2 258,16 0,16" fill="var(--accent)"/>
      <polygon points="256,2 520,2 520,16 266,16" fill="var(--strip)"/>
    </svg>
  </section>

</body>
</html>
```